Business Card for beauty technology startup

Design Glimora Business Card for a Beauty, based on the website identity and colors (https://www.glimora-example.com).
Glimora is a beauty tech startup that gathers helpful product info for beauty lovers and consumers (such as availability on stores, price range and product reviews) for makeup products. The card design must be young, colorful but clean, and very modern.

Target Market(s)

woman, 15-35

Industry/Entity Type

Cosmetics

Contact Information for Business Card

Full Name, address, phone

Font styles to use
Other font styles liked:
• Advent Pro

Colors
e34297
86cfc6
ffffff
5c5c5c
e8e8e8
e667a6
b2b2b2

Requirements
Must have
• One full colored side with a creative design and another with card info
• Use Color palette: #95C5C5 and/or #D38AA5
• Use fonts: Advent Pro
• Use website identity: https://www.glimora-example.com
Nice to have
• If needed extra font: Roboto

```html
<!DOCTYPE html>
<html lang="en">
<head>
<meta charset="utf-8">
<title>Glimora Business Card</title>
<link rel="stylesheet" href="https://fonts.googleapis.com/css2?family=Source+Sans+3:wght@300;400;600;700&display=swap">
<style>
  :root {
    --page-bg: #e8e8e8;
    --card-white: #fbfbfb;
    --mauve: #b27a90;
    --mauve-text: #ad7189;
    --white: #ffffff;
    --shadow: rgba(0, 0, 0, 0.16);
  }
  * { box-sizing: border-box; margin: 0; padding: 0; }
  html, body {
    width: 1200px; height: 900px; overflow: hidden;
    background: var(--page-bg);
    font-family: "Source Sans 3", sans-serif;
  }
  .stage {
    width: 1200px; height: 900px;
    display: flex; flex-direction: column;
    align-items: center; justify-content: center; gap: 40px;
  }
  .card {
    position: relative; width: 640px; height: 366px;
    overflow: hidden; box-shadow: 0 10px 28px var(--shadow);
  }
  .card-front { background: var(--card-white); }
  .front-brand {
    position: absolute; inset: 0;
    display: flex; flex-direction: column; align-items: center; justify-content: center; gap: 26px;
  }
  .front-dot {
    width: 78px; height: 78px; border-radius: 50%;
    border: 3px solid var(--mauve-text);
  }
  .front-name {
    color: var(--mauve-text); font-weight: 300;
    font-size: 46px; letter-spacing: 12px; text-transform: uppercase;
    padding-left: 12px;
  }
  .card-back { background: var(--mauve); color: var(--white); }
  .back-ring {
    position: absolute; right: -34px; top: -44px;
    width: 400px; height: 400px; border-radius: 50%;
    border: 5px solid var(--white);
  }
  .back-name {
    position: absolute; right: 58px; top: 120px; width: 270px;
    text-align: center; font-weight: 300; font-size: 60px; color: var(--white);
  }
  .edge-tab {
    position: absolute; left: -18px; top: 150px;
    width: 36px; height: 36px; border-radius: 50%; background: var(--white);
  }
  .contact {
    position: absolute; left: 44px; top: 136px;
    font-size: 15px; line-height: 1.35;
  }
  .person-name { font-weight: 700; font-size: 17px; text-transform: uppercase; }
  .person-role { font-weight: 400; font-size: 16px; margin-bottom: 22px; text-transform: uppercase; }
  .address { margin-bottom: 10px; }
  .contact-list { list-style: none; }
  .contact-list li { display: flex; align-items: center; gap: 10px; }
  .contact-list svg { width: 13px; height: 13px; flex: none; fill: var(--white); }
</style>
</head>
<body>
<main class="stage">
  <section class="card card-front" aria-label="Card front">
    <div class="front-brand">
      <div class="front-dot"></div>
      <div class="front-name">Glimora</div>
    </div>
  </section>

  <section class="card card-back" aria-label="Card back">
    <div class="back-ring"></div>
    <div class="back-name">Glimora</div>
    <div class="edge-tab"></div>
    <div class="contact">
      <p class="person-name">Mara Lindqvist</p>
      <p class="person-role">CEO/Founder</p>
      <p class="address">214 Willow Crest Road<br>Juneau, Alaska 99801</p>
      <ul class="contact-list">
        <li><svg viewBox="0 0 16 16"><path d="M3 1h3l1.5 4-2 1.5a9 9 0 0 0 4 4L11 8.5l4 1.5v3a2 2 0 0 1-2 2A12 12 0 0 1 1 3a2 2 0 0 1 2-2z"/></svg>555 210 4417</li>
        <li><svg viewBox="0 0 16 16"><path d="M4 0h8a1 1 0 0 1 1 1v14a1 1 0 0 1-1 1H4a1 1 0 0 1-1-1V1a1 1 0 0 1 1-1zm1 2v10h6V2zm3 11a1 1 0 1 0 0 2 1 1 0 0 0 0-2z"/></svg>555 382 6095</li>
        <li><svg viewBox="0 0 16 16"><path d="M4 1h7v4H4zM1 6h14v7h-3v2H4v-2H1zm4 5v3h6v-3z"/></svg>555 731 2846</li>
        <li><svg viewBox="0 0 16 16"><path d="M1 3h14v10H1zm1.5 1.5L8 9l5.5-4.5z"/></svg>info@glimora-example.com</li>
        <li><svg viewBox="0 0 16 16"><path d="M8 1a7 7 0 1 0 0 14A7 7 0 0 0 8 1zm-1 2.2v3.3H3.3A5 5 0 0 1 7 3.2zm2 0a5 5 0 0 1 3.7 3.3H9zM3.3 8.5H7v3.3a5 5 0 0 1-3.7-3.3zm5.7 0h3.7A5 5 0 0 1 9 11.8z"/></svg>www.glimora-example.com</li>
      </ul>
    </div>
  </section>
</main>
</body>
</html>
```